Chamber of Commerce Web Design Project

We are working with Harborlight Chamber of Commerce. They are a new chamber of commerce forming in SoCal.
Some sites to use for inspiration:
https://brevinmarchamber.org
https://quellford.org
https://www.dorwickhavenchamber.com
https://www.tpchamber.com
https://velmorintcc.org
Thank you for taking the time to consider designing a website for us. We are web developers based in Stockton, CA, USA. Most of our projects go through the same process. Understanding this process may help you win a project with us. We custom-code all of our websites in-house. We don’t have any requirements as to what tools you use for your design, but we prefer Figma files. For any design that we label as four-stars, we send it to the client for review. The client picks the final design they want us to use. Once we complete this process, we will continue to show additional clients all the four-star sites and purchase them later. Your designs will have multiple chances to sell. For better chances of success, we ask that you follow these guidelines.
IMAGES:
If you use any images or icons in the design, we ask that you have a link to the asset so we can purchase the image/icon. Most of the designs we submit do not have the customer’s images on them unless they have some great images. Be creative; show us the feeling you are trying to portray with your image choices. Use any royalty-free site you choose. We subscribe to Adobe and mainly use their images, but we can purchase images outside of Adobe.
PLEASE NOTE: we will not submit designs to clients with watermarks on the images.
FONTS:
We ask that you identify the fonts used in the design. This can be done in a message if you want. We typically use plain rating dot Fonts and Adobe Fonts.
CONTENT:
We're always open to different content and ideas. We often submit designs with stock images so the client can see our vision. We typically take pictures after the website launch to use their images with our vision. Lorem Ipsum is fine for paragraphs, but we ask that you write the headers in correct English. We want to be able to show the vision and identify the sections of the website.
INSPIRATION:
We typically add a couple of links in the brief of websites we like to help you get started in your design.
REVISIONS:
We do not often ask for revisions of the designs unless we see something in the design that may not appeal to the client. If there are slight changes that we want to make, we do that in the development process.
FEEDBACK:
We rarely give feedback on designs during the design process. We are working on many website projects and do not have the time to provide feedback. We usually respond if your request is well thought out and asks specific questions, but a note asking “feedback, please” usually goes unanswered.

```html
<!DOCTYPE html>
<html lang="en">
<head>
<meta charset="utf-8">
<title>Harborlight Chamber of Commerce</title>
<link rel="stylesheet" href="https://fonts.googleapis.com/css2?family=Oswald:wght@500;700&family=Poppins:wght@300;400;500;600;700&display=swap">
<style>
:root{
  --blue:#0b8cf1;
  --blue-deep:#0677d6;
  --yellow:#fcd43a;
  --ink:#2a2a2a;
  --text:#666;
  --grey:#9c9c9c;
  --card:#f2f2f2;
  --black:#050505;
}
*{box-sizing:border-box;margin:0;padding:0}
html,body{width:1200px;height:4011px;overflow:hidden;background:#fff}
body{position:relative;font-family:'Poppins',sans-serif;color:var(--ink)}
.abs{position:absolute}
.head-font{font-family:'Oswald',sans-serif;font-weight:700;text-transform:uppercase}
.btn{position:absolute;display:flex;align-items:center;justify-content:center;gap:8px;background:var(--blue);color:#fff;font-weight:600;font-size:14px;border-radius:30px;text-transform:uppercase;box-shadow:0 3px 8px rgba(0,0,0,.15)}
.btn .dot{width:12px;height:12px;border-radius:50%;background:#fff;display:inline-block;position:relative}
.btn .dot::after{content:"";position:absolute;left:3px;top:3px;border-left:6px solid var(--blue);border-top:3px solid transparent;border-bottom:3px solid transparent}

/* header */
.topbar{left:510px;top:0;width:690px;height:55px;background:var(--yellow);clip-path:polygon(0 0,100% 0,100% 100%,30px 100%)}
.contact-chip{display:flex;align-items:center;gap:12px;font-size:15px;font-weight:600;color:#111;top:8px}
.chip-ic{width:40px;height:40px;border-radius:50%;background:#111;display:flex;align-items:center;justify-content:center}
.brand{display:flex;align-items:center;gap:10px}
.brand-mark{width:52px;height:52px;border-radius:50%;background:var(--blue)}
.brand-name{font-family:'Oswald',sans-serif;font-weight:700;color:var(--blue);text-transform:uppercase;line-height:1}
.nav{display:flex;gap:26px;font-size:13px;font-weight:600;text-transform:uppercase;color:#111}
.nav .active{color:var(--blue)}
.login{left:965px;top:73px;width:125px;height:45px;background:#8e8e8e;border-radius:24px;color:#fff;font-size:13px;font-weight:600;display:flex;align-items:center;justify-content:center;gap:6px}

/* hero */
.hero{left:0;top:137px;width:1200px;height:554px;background:linear-gradient(180deg,#c9a27a 0%,#a48872 30%,#6a6660 65%,#3f4246 100%)}
.hero h1{position:absolute;left:108px;top:165px;color:#fff;font-size:58px;line-height:74px;letter-spacing:.5px;text-shadow:0 2px 6px rgba(0,0,0,.35)}
.hero .btn{left:108px;top:333px;width:222px;height:52px;border:3px solid #fff}
.slides{left:120px;top:505px;display:flex;gap:10px}
.slides span{width:75px;height:3px;background:rgba(255,255,255,.6)}
.slides span+span{background:#fff}

/* section titles */
.title{position:absolute;left:0;width:1200px;text-align:center;font-size:44px;color:#333}
.title b{color:var(--blue);font-weight:700}
.rule{position:absolute;width:66px;height:4px;background:#222;left:567px}

/* about */
.about-photo{left:113px;top:810px;width:440px;height:440px;border-radius:50%;background:radial-gradient(circle at 50% 40%,#c9c2ba,#5d6d83 70%,#3b4a62);box-shadow:0 10px 25px rgba(0,0,0,.15)}
.about-title{left:636px;top:850px;font-size:44px;color:#333}
.about-title b{color:var(--blue)}
.about-text{left:636px;top:942px;width:450px;font-size:14.5px;line-height:26px;color:var(--text)}

/* programs */
.programs{left:0;top:1353px;width:1200px;height:644px;background:linear-gradient(135deg,var(--blue) 0%,#1a95f5 50%,var(--blue) 100%)}
.prog-card{position:absolute;top:208px;width:235px;height:309px;background:var(--card);border-radius:3px;text-align:center;padding:40px 22px 0}
.prog-card.on{border-bottom:5px solid var(--yellow)}
.prog-ic{width:88px;height:88px;border-radius:50%;background:var(--blue);margin:0 auto 22px;display:flex;align-items:center;justify-content:center}
.prog-card.on .prog-ic{background:var(--yellow)}
.prog-card h3{font-size:16px;font-weight:600;line-height:24px;color:#222}
.prog-card p{font-size:13.5px;line-height:24px;color:#777;margin-top:12px}

/* events */
.arrow{position:absolute;width:54px;height:54px;border-radius:50%;background:#fff;box-shadow:0 2px 10px rgba(0,0,0,.15);display:flex;align-items:center;justify-content:center;font-size:20px;color:#444;font-weight:700}
.event{position:absolute;top:2191px;width:296px;height:354px;background:#fff;box-shadow:0 2px 14px rgba(0,0,0,.14);text-align:center}
.event.on{border:2px solid #777;box-shadow:none;height:372px}
.event .img{position:absolute;left:8px;top:8px;right:8px;height:184px}
.event .date{position:absolute;left:50%;transform:translateX(-50%);top:178px;background:#111;color:#fff;font-size:11px;font-weight:600;padding:4px 14px;border-radius:10px}
.event h3{position:absolute;top:210px;width:100%;font-size:18.5px;font-weight:600;color:#111}
.event p{position:absolute;top:246px;left:20px;right:20px;font-size:14.5px;line-height:26px;color:#777}
.event .btn{left:64px;top:332px;width:167px;height:45px}
.event.on .btn{background:#7d7d7d;top:346px}

/* partners */
.partners{left:0;top:2703px;width:1200px;height:315px;background:var(--grey)}
.partner{position:absolute;top:112px;width:92px;height:92px;border:6px solid #fff;opacity:.9}

/* testimonials */
.review{position:absolute;top:3205px;width:315px;height:229px;background:#fff;box-shadow:0 2px 12px rgba(0,0,0,.12);padding:28px 25px}
.review .who{display:flex;align-items:center;gap:14px}
.avatar{width:64px;height:64px;border-radius:50%;background:linear-gradient(135deg,#9aa3ad,#3f4955)}
.who strong{display:block;font-size:15.5px;font-weight:500;color:#222}
.who small{font-size:13px;color:#555}
.rating{margin-left:auto;display:flex;align-items:center;gap:5px;margin-top:-18px}
.rating i{width:14px;height:14px;border-radius:50%;border:2px solid #999;display:block}
.rating span{color:#f2b91e;font-size:11px;letter-spacing:1px}
.review p{margin-top:24px;font-size:12.5px;line-height:22px;color:#333}

/* footer */
.footer{left:0;top:3510px;width:1200px;height:501px}
.f-nav{left:0;top:3693px;width:1200px;display:flex;justify-content:center;gap:27px;font-size:13.5px;font-weight:600;color:#fff;text-transform:uppercase}
.f-line{left:168px;width:840px;height:1px;background:#555}
.f-item{display:flex;gap:22px;color:#fff}
.f-ic{width:50px;height:50px;border-radius:50%;border:2px solid #fff;display:flex;align-items:center;justify-content:center;flex:none}
.f-item h4{font-size:13.5px;font-weight:600;text-transform:uppercase;margin-bottom:8px;padding-top:4px}
.f-item p{font-size:14.5px;line-height:23px}
.social{left:522px;top:3880px;display:flex;gap:10px}
.social span{width:40px;height:40px;border-radius:50%;background:#fff;border:2px solid #333}
.copy{left:0;top:3962px;width:1200px;text-align:center;color:#fff;font-size:12.5px}
</style>
</head>
<body>

<!-- header -->
<header>
  <div class="abs topbar"></div>
  <div class="abs contact-chip" style="left:603px">
    <span class="chip-ic"><svg width="18" height="18" viewBox="0 0 24 24"><path fill="#fff" d="M6.6 10.8a15 15 0 006.6 6.6l2.2-2.2c.3-.3.7-.4 1-.2 1.1.4 2.3.6 3.6.6.6 0 1 .4 1 1V20c0 .6-.4 1-1 1A17 17 0 013 4c0-.6.4-1 1-1h3.5c.6 0 1 .4 1 1 0 1.3.2 2.5.6 3.6.1.3 0 .7-.2 1z"/></svg></span>+1(8888) 888 888
  </div>
  <div class="abs contact-chip" style="left:833px">
    <span class="chip-ic"><svg width="18" height="14" viewBox="0 0 24 18"><path fill="#fff" d="M0 2l12 8 12-8V0H0zm0 3v13h24V5l-12 8z"/></svg></span>info@Companyname.com
  </div>
  <div class="abs brand" style="left:110px;top:35px">
    <span class="brand-mark"></span>
    <span><span class="brand-name" style="font-size:26px;display:block">Harborlight</span><span style="font-size:12px;font-weight:600;color:var(--blue);text-transform:uppercase">Chamber of Commerce</span></span>
  </div>
  <nav class="abs nav" style="left:363px;top:90px">
    <span class="active">Home</span><span>About</span><span>Membership ˅</span><span>Event</span><span>Business Directory</span><span>Contact</span>
  </nav>
  <div class="abs login"><svg width="12" height="12" viewBox="0 0 24 24"><circle cx="12" cy="7" r="5" fill="#fff"/><path fill="#fff" d="M2 24c0-6 4-10 10-10s10 4 10 10z"/></svg>LOG IN</div>
</header>

<!-- hero -->
<section class="abs hero" role="img" aria-label="Sunset view over a city boulevard lined with palm trees and a historic tower">
  <h1 class="head-font">Empowering Businesses.<br>Strengthening Communities</h1>
  <span class="btn">Join the Chamber <i class="dot"></i></span>
  <div class="abs slides" style="top:505px;left:120px"><span></span><span></span><span></span></div>
</section>

<!-- about -->
<section>
  <div class="abs about-photo" role="img" aria-label="Team of smiling business professionals in an office"></div>
  <h2 class="abs head-font about-title">About <b>Us</b></h2>
  <div class="abs" style="left:636px;top:910px;width:66px;height:4px;background:#222"></div>
  <p class="abs about-text">Sed ut perspiciatis unde omnis iste natus error sit voluptatem accusantium doloremque laudantium, totam rem aperiam, eaque ipsa quae ab illo inventore veritatis et quasi architecto beatae vitae dicta sunt explicabo. Nemo enim ipsam voluptatem quia voluptas sit aspernatur aut odit aut fugit, sed quia consequuntur magni dolores eos qui ratione voluptatem sequi nesciunt. Neque porro quisquam est, qui</p>
  <span class="btn" style="left:636px;top:1145px;width:161px;height:48px">View More <i class="dot"></i></span>
</section>

<!-- programs -->
<section class="abs programs">
  <h2 class="head-font" style="position:absolute;top:100px;width:1200px;text-align:center;font-size:44px;color:#fff">Our Programs</h2>
  <div class="prog-card" style="left:103px">
    <div class="prog-ic"><svg width="40" height="40" viewBox="0 0 40 40" fill="none" stroke="#fff" stroke-width="2"><circle cx="20" cy="20" r="16"/><path d="M12 18l8-5 8 5-8 5z"/><path d="M15 21v5c3 2 7 2 10 0v-5"/></svg></div>
    <h3>Business Education Alliance</h3>
    <p>Working with over 20 large and small lenders, property developers</p>
  </div>
  <div class="prog-card on" style="left:362px">
    <div class="prog-ic"><svg width="40" height="40" viewBox="0 0 40 40" fill="none" stroke="#222" stroke-width="2"><circle cx="20" cy="17" r="12"/><path d="M20 10l2 5h5l-4 3 2 5-5-3-5 3 2-5-4-3h5z"/><path d="M13 27l-3 9 5-2 3 4 2-8M27 27l3 9-5-2-3 4-2-8"/></svg></div>
    <h3>Certificates of Origin</h3>
    <p style="margin-top:6px">We have grown and changed with the industry, and we're dedicated</p>
    <svg width="16" height="16" viewBox="0 0 16 16" style="margin-top:12px"><circle cx="8" cy="8" r="8" fill="#111"/><path d="M6 4l5 4-5 4z" fill="#fff"/></svg>
  </div>
  <div class="prog-card" style="left:620px">
    <div class="prog-ic"><svg width="40" height="40" viewBox="0 0 40 40" fill="none" stroke="#fff" stroke-width="2"><rect x="8" y="6" width="20" height="26"/><path d="M12 12h12M12 17h8"/><circle cx="25" cy="24" r="6"/><path d="M29 28l5 5"/></svg></div>
    <h3 style="font-size:17px">Government Relations Council</h3>
    <p>When we say we care, we mean it. If you are a client now we want you</p>
  </div>
  <div class="prog-card" style="left:879px">
    <div class="prog-ic"><svg width="40" height="40" viewBox="0 0 40 40" fill="none" stroke="#fff" stroke-width="2"><rect x="14" y="6" width="18" height="22"/><path d="M18 12h10M18 16h10M18 20h6"/><circle cx="12" cy="26" r="5"/><circle cx="24" cy="33" r="2"/><circle cx="30" cy="33" r="2"/></svg></div>
    <h3 style="font-size:17px">Green Team Coastal Valley</h3>
    <p>Our team of finance, property investment and accounting experts</p>
  </div>
</section>

<!-- events -->
<section>
  <h2 class="title head-font" style="top:2090px">Our <b>Events</b></h2>
  <div class="rule" style="top:2150px"></div>
  <span class="arrow" style="left:30px;top:2364px">«</span>
  <span class="arrow" style="left:1110px;top:2364px;color:#6cab2a">»</span>

  <article class="event" style="left:112px">
    <div class="img" role="img" aria-label="Colleagues meeting around a table with laptops" style="background:linear-gradient(135deg,#e5e2dc,#8c8a86)"></div>
    <span class="date">Nov 12,2024</span>
    <h3>LORUM IPSUM DOLOR</h3>
    <p>Sed ut perspiciatis unde omnis iste natus error sit voluptatem accusantium doloremque</p>
    <span class="btn">View More <i class="dot"></i></span>
  </article>
  <article class="event on" style="left:447px">
    <div class="img" role="img" aria-label="City skyline of glass towers under a cloudy sky" style="background:linear-gradient(180deg,#c7cfd6,#6c7f8e 60%,#3e4f5c)"></div>
    <span class="date">Nov 12,2024</span>
    <h3>LORUM IPSUM DOLOR</h3>
    <p>Sed ut perspiciatis unde omnis iste natus error sit voluptatem accusantium doloremque</p>
    <span class="btn">View More <i class="dot" style="--x:0"></i></span>
  </article>
  <article class="event" style="left:784px">
    <div class="img" role="img" aria-label="Downtown skyline at golden hour" style="background:linear-gradient(180deg,#d9c9b6,#9a8673 60%,#5e5349)"></div>
    <span class="date">Nov 12,2024</span>
    <h3>LORUM IPSUM DOLOR</h3>
    <p>Sed ut perspiciatis unde omnis iste natus error sit voluptatem accusantium doloremque</p>
    <span class="btn">View More <i class="dot"></i></span>
  </article>
</section>

<!-- partners -->
<section class="abs partners" aria-label="Partner organisations">
  <span class="partner" style="left:118px"></span>
  <span class="partner" style="left:336px;border-radius:50%"></span>
  <span class="partner" style="left:555px"></span>
  <span class="partner" style="left:774px;border-radius:50%"></span>
  <span class="partner" style="left:992px"></span>
</section>

<!-- testimonials -->
<section>
  <h2 class="title head-font" style="top:3100px">Our <b>Testimonials</b></h2>
  <div class="rule" style="top:3162px"></div>
  <span class="arrow" style="left:33px;top:3303px">«</span>
  <span class="arrow" style="left:1113px;top:3303px;color:#6cab2a">»</span>

  <article class="review" style="left:113px">
    <div class="who"><span class="avatar" role="img" aria-label="Reviewer portrait"></span><span><strong>Marlo Threnn</strong><small>Manager</small></span><span class="rating"><i></i><span>★★★★★</span></span></div>
    <p>Lorem ipsum dolor sit amet, consectetur adipiscing elit, sed do eiusmod tempor incididunt ut labore et dolore magna aliqua. Ut enim ad minim veniamea .</p>
  </article>
  <article class="review" style="left:443px">
    <div class="who"><span class="avatar" role="img" aria-label="Reviewer portrait" style="background:linear-gradient(135deg,#e6ded6,#8a7360)"></span><span><strong>Ilsa Dorvane</strong><small>Manager</small></span><span class="rating"><i></i><span>★★★★★</span></span></div>
    <p>Lorem ipsum dolor sit amet, consectetur adipiscing elit, sed do eiusmod tempor incididunt ut labore et dolore magna aliqua. Ut enim ad minim veniamea .</p>
  </article>
  <article class="review" style="left:772px">
    <div class="who"><span class="avatar" role="img" aria-label="Reviewer portrait" style="background:linear-gradient(135deg,#8aa0b8,#26323f)"></span><span><strong>Teodor Quall</strong><small>Manager</small></span><span class="rating"><i></i><span>★★★★★</span></span></div>
    <p>Lorem ipsum dolor sit amet, consectetur adipiscing elit, sed do eiusmod tempor incididunt ut labore et dolore magna aliqua. Ut enim ad minim veniamea .</p>
  </article>
</section>

<!-- footer -->
<footer>
  <svg class="abs footer" viewBox="0 0 1200 501" preserveAspectRatio="none">
    <path d="M0 80 Q600 -20 1200 80 V501 H0Z" fill="var(--yellow)"/>
    <path d="M0 105 Q600 0 1200 105 V501 H0Z" fill="var(--black)"/>
  </svg>
  <div class="abs brand" style="left:450px;top:3598px">
    <span class="brand-mark" style="width:60px;height:60px"></span>
    <span><span class="brand-name" style="font-size:34px;display:block">Harborlight</span><span style="font-size:14px;font-weight:600;color:var(--blue);text-transform:uppercase">Chamber of Commerce</span></span>
  </div>
  <nav class="abs f-nav"><span>Home</span><span>About</span><span>Membership ˅</span><span>Event</span><span>Business Directory</span><span>Contact</span></nav>
  <div class="abs f-line" style="top:3737px"></div>

  <div class="abs f-item" style="left:150px;top:3770px">
    <span class="f-ic"><svg width="16" height="20" viewBox="0 0 16 22"><path fill="#fff" d="M8 0a8 8 0 00-8 8c0 6 8 14 8 14s8-8 8-14a8 8 0 00-8-8zm0 11a3 3 0 110-6 3 3 0 010 6z"/></svg></span>
    <div><h4>Location</h4><p>Lorem ipsum dolor sit amet,<br>consectetur adipiscing elit,<br>sed do eiusmod.</p></div>
  </div>
  <div class="abs f-item" style="left:535px;top:3770px">
    <span class="f-ic"><svg width="18" height="18" viewBox="0 0 24 24"><path fill="#fff" d="M6.6 10.8a15 15 0 006.6 6.6l2.2-2.2c.3-.3.7-.4 1-.2 1.1.4 2.3.6 3.6.6.6 0 1 .4 1 1V20c0 .6-.4 1-1 1A17 17 0 013 4c0-.6.4-1 1-1h3.5c.6 0 1 .4 1 1 0 1.3.2 2.5.6 3.6.1.3 0 .7-.2 1z"/></svg></span>
    <div><h4>Phone</h4><p>+1(8888) 888 888</p></div>
  </div>
  <div class="abs f-item" style="left:843px;top:3770px">
    <span class="f-ic"><svg width="18" height="14" viewBox="0 0 24 18"><path fill="#fff" d="M0 2l12 8 12-8V0H0zm0 3v13h24V5l-12 8z"/></svg></span>
    <div><h4>Email</h4><p>info@companyname.com</p></div>
  </div>

  <div class="abs f-line" style="top:3900px"></div>
  <div class="abs social"><span></span><span></span><span></span></div>
  <p class="abs copy">Copyright@2024. All Rights Reserved</p>
</footer>

</body>
</html>
```